Alterations to existing business card

Here is my current logo and I want the "cafe and bar" taken off with just the words Lumo and our slogan "Savour the moment" on the card, Plus the logo.
Our Current Business Card is currently 5.5cm by 5.5cm and would like it to remain like this thanks.
The loyalty card can be 10 squares with the logo specifying the 10th coffee free. I would like the cheapest option please.
Also on our business card would like the Facebook logo and instagram Logo with TAZALUMO27 as link to our photos on instagram.

Keep Colour schemes the same please.

On the business cards

Dale Brinton Director
0427916038
dale27lumo@mailvista.test

Paula Ferrisi Principal
0428571963
paulumo@mailvista.test

Thanks Dale

Industry/Entity Type

Business

```html
<!DOCTYPE html>
<html lang="en">
<head>
<meta charset="utf-8">
<title>Lumo — Business &amp; Loyalty Cards</title>
<link rel="stylesheet" href="https://fonts.googleapis.com/css2?family=Open+Sans:wght@300;400;600&display=swap">
<style>
  :root {
    --backdrop: #ecebe8;
    --card: #ffffff;
    --gold: #e2a12c;
    --gold-light: #f3cf72;
    --ink: #1c1c1c;
    --shadow: rgba(0, 0, 0, 0.14);
  }
  * { box-sizing: border-box; margin: 0; padding: 0; }
  html, body {
    width: 1200px; height: 900px; overflow: hidden;
    background: var(--backdrop);
    font-family: "Open Sans", Arial, sans-serif;
  }
  .canvas { position: relative; width: 1200px; height: 900px; }
  .card {
    position: absolute;
    width: 325px; height: 325px;
    background: var(--card);
    box-shadow: 0 6px 22px var(--shadow);
  }
  .card--contact { left: 229px; top: 70px; }
  .card--loyalty { left: 690px; top: 528px; }

  /* contact card */
  .social { position: absolute; left: 29px; top: 53px; display: flex; gap: 10px; }
  .social__dot { width: 28px; height: 28px; border: 2.5px solid var(--ink); border-radius: 50%; }

  .brand { position: absolute; left: 196px; top: 20px; width: 110px; text-align: center; }
  .brand__ring {
    width: 80px; height: 80px; margin: 0 auto 8px;
    border: 3px solid var(--gold); border-radius: 50%;
  }
  .brand__name { font-weight: 400; font-size: 24px; letter-spacing: 1.5px; line-height: 1; color: var(--ink); }
  .brand__slogan { font-size: 6.5px; letter-spacing: 0.5px; color: var(--gold); margin-top: 3px; white-space: nowrap; }

  .person { position: absolute; left: 29px; font-size: 14.5px; color: var(--ink); line-height: 20px; }
  .person--first { top: 102px; }
  .person--second { top: 206px; }
  .person__name { color: var(--gold); font-size: 15px; }
  .person__role { margin-bottom: 9px; }
  .contact-line { display: flex; align-items: center; gap: 7px; }
  .contact-line svg { width: 11px; height: 11px; fill: var(--gold); flex: none; }

  /* loyalty card */
  .loyalty__name {
    position: absolute; left: 0; right: 0; top: 36px;
    text-align: center; font-weight: 300; font-size: 82px; line-height: 1;
    letter-spacing: 2px; color: var(--ink);
  }
  .loyalty__slogan {
    position: absolute; left: 0; right: 0; top: 115px;
    text-align: center; font-size: 17px; letter-spacing: 2px; color: var(--gold);
    white-space: nowrap;
  }
  .stamps {
    position: absolute; left: 23px; top: 171px;
    display: grid; grid-template-columns: repeat(5, 50px); column-gap: 6px; row-gap: 20px;
  }
  .stamp {
    width: 50px; height: 50px; border-radius: 50%;
    background: radial-gradient(circle, #fff 58%, var(--gold-light) 62%, var(--gold) 72%, #fff 76%);
    box-shadow: 0 0 0 1px var(--gold-light);
    display: flex; align-items: center; justify-content: center;
  }
  .stamp--free { font-size: 12px; color: var(--gold); letter-spacing: 0.3px; }
</style>
</head>
<body>
<main class="canvas">

  <section class="card card--contact" aria-label="Lumo business card">
    <div class="social" aria-label="Social media links">
      <span class="social__dot"></span>
      <span class="social__dot"></span>
    </div>

    <div class="brand">
      <div class="brand__ring"></div>
      <div class="brand__name">LUMO</div>
      <div class="brand__slogan">SAVOUR THE MOMENT</div>
    </div>

    <div class="person person--first">
      <div class="person__name">Dale Brinton</div>
      <div class="person__role">Director</div>
      <div class="contact-line">
        <svg viewBox="0 0 24 24" aria-hidden="true"><path d="M6.6 10.8a15.1 15.1 0 0 0 6.6 6.6l2.2-2.2a1 1 0 0 1 1-.25 11.4 11.4 0 0 0 3.6.57 1 1 0 0 1 1 1V20a1 1 0 0 1-1 1A17 17 0 0 1 3 4a1 1 0 0 1 1-1h3.5a1 1 0 0 1 1 1c0 1.25.2 2.450.57 3.57a1 1 0 0 1-.25 1z"/></svg>
        <span>0427916038</span>
      </div>
      <div class="contact-line">
        <svg viewBox="0 0 24 24" aria-hidden="true"><path d="M2 5h20v14H2z M3 6l9 7 9-7" stroke="#fff" stroke-width="1.6"/></svg>
        <span>dale27lumo@mailvista.test</span>
      </div>
    </div>

    <div class="person person--second">
      <div class="person__name">Paula Ferrisi</div>
      <div class="person__role">Principal</div>
      <div class="contact-line">
        <svg viewBox="0 0 24 24" aria-hidden="true"><path d="M6.6 10.8a15.1 15.1 0 0 0 6.6 6.6l2.2-2.2a1 1 0 0 1 1-.25 11.4 11.4 0 0 0 3.6.57 1 1 0 0 1 1 1V20a1 1 0 0 1-1 1A17 17 0 0 1 3 4a1 1 0 0 1 1-1h3.5a1 1 0 0 1 1 1c0 1.25.2 2.45.57 3.57a1 1 0 0 1-.25 1z"/></svg>
        <span>0428571963</span>
      </div>
      <div class="contact-line">
        <svg viewBox="0 0 24 24" aria-hidden="true"><path d="M2 5h20v14H2z M3 6l9 7 9-7" stroke="#fff" stroke-width="1.6"/></svg>
        <span>paulumo@mailvista.test</span>
      </div>
    </div>
  </section>

  <section class="card card--loyalty" aria-label="Lumo loyalty card">
    <div class="loyalty__name">LUMO</div>
    <div class="loyalty__slogan">SAVOUR THE MOMENT</div>
    <div class="stamps">
      <span class="stamp"></span><span class="stamp"></span><span class="stamp"></span><span class="stamp"></span><span class="stamp"></span>
      <span class="stamp"></span><span class="stamp"></span><span class="stamp"></span><span class="stamp"></span>
      <span class="stamp stamp--free">FREE</span>
    </div>
  </section>

</main>
</body>
</html>
```